Social Media App Needs PPT Template

We need a PowerPoint template for a new social media company based in the DC area called "Bold Ledger." We provide an interactive digital platform for executives to share actionable advice. We would like to see designs that use our orange logo color as an accent, but are mainly grey, white, and black. The final design should communicate clean, chic, modern, and professional.

Target Market(s)

Executives

Industry/Entity Type

Information Technology

Font styles to use
Sans Serif

Colors
f78f20
fbe7d2
ffffff
000000
e8e8e8
757575

Requirements
Must have
• My project must have title page and many options for the body of the ppt (graphs, tables, etc). It also needs to be easy to modify. I must have someone who is experienced in creating powerpoint templates.
Nice to have
• It would be nice to have a very modern and clean design that includes the logo on every page, but still leaves a lot of room for the content of the slide
Should not have
• My design project should not look to busy.

```html
<!DOCTYPE html>
<html lang="en">
<head>
<meta charset="utf-8">
<title>Bold Ledger – Content Slide</title>
<link href="https://fonts.googleapis.com/css2?family=Lato:wght@300;400;700&display=swap" rel="stylesheet">
<style>
  :root {
    --stage-grey: #cccccc;
    --navy: #222d3b;
    --orange: #f7901e;
    --white: #ffffff;
    --ink: #2b2f36;
    --muted: #757575;
    --rule-navy: #3c4658;
  }
  * { margin: 0; padding: 0; box-sizing: border-box; }
  html, body {
    width: 1200px; height: 960px; overflow: hidden;
    background: var(--stage-grey);
    font-family: "Lato", Arial, sans-serif;
  }
  .page-label {
    position: absolute; top: 64px; left: 0; width: 1200px;
    text-align: center; color: var(--white);
    font-weight: 300; font-size: 32px; letter-spacing: 0.5px;
  }
  .slide {
    position: absolute; left: 120px; top: 143px;
    width: 958px; height: 718px; background: var(--white);
  }
  .sidebar {
    position: absolute; left: 0; top: 0; width: 170px; height: 100%;
    background: var(--navy);
  }
  .brand {
    position: absolute; top: 44px; left: 0; width: 170px;
    display: flex; flex-direction: column; align-items: center; gap: 14px;
  }
  .brand-dot {
    width: 38px; height: 38px; border-radius: 50%; background: var(--orange);
  }
  .brand-name {
    color: var(--white); font-weight: 700; font-size: 24px; line-height: 1.1;
    text-align: center; letter-spacing: 0.5px;
  }
  .site-url {
    position: absolute; left: 19px; bottom: 22px;
    color: var(--white); font-weight: 300; font-size: 17.5px;
  }
  .slide-title {
    position: absolute; left: 205px; top: 92px;
    color: var(--orange); font-weight: 400; font-size: 42px; line-height: 50px;
  }
  .title-rule {
    position: absolute; left: 205px; top: 154px; width: 715px; height: 1px;
    background: var(--orange);
  }
  .feature {
    position: absolute; top: 250px; width: 208px;
  }
  .feature-icon {
    display: block; height: 90px; margin: 0 auto 34px;
  }
  .feature-text {
    color: var(--ink); font-size: 14.4px; line-height: 20.2px;
    text-align: justify; text-align-last: center; hyphens: manual;
  }
  .feature--one { left: 210px; }
  .feature--two { left: 464px; }
  .feature--three { left: 718px; }
  .footer-rule {
    position: absolute; left: 802px; top: 664px; width: 124px; height: 1px;
    background: var(--rule-navy);
  }
  .page-number {
    position: absolute; right: 36px; top: 681px;
    color: var(--muted); font-size: 13px;
  }
</style>
</head>
<body>
  <div class="page-label">Page 3</div>

  <section class="slide">
    <aside class="sidebar">
      <div class="brand">
        <span class="brand-dot"></span>
        <span class="brand-name">Bold Ledger</span>
      </div>
      <div class="site-url">boldledger.com</div>
    </aside>

    <h1 class="slide-title">Title of the page</h1>
    <div class="title-rule"></div>

    <article class="feature feature--one">
      <svg class="feature-icon" viewBox="0 0 112 90" width="112" fill="none" stroke="#222d3b" stroke-width="3.5" stroke-linejoin="round" stroke-linecap="round">
        <rect x="5" y="6" width="102" height="68" rx="2"/>
        <rect x="12" y="12" width="88" height="55"/>
        <polyline points="29,46 42,36 56,44 77,26"/>
        <path d="M1 74 H111 V81 H1 Z"/>
      </svg>
      <p class="feature-text">Duis autem vel eum iriure dolor in hendrerit in vulputate velit esse molestie consequat, vel illum dolore eu feugiat nulla facilisis at vero eros et accumsan et iusto odio dignissim qui blan&shy;dit praesent luptatum zzril del enit augue duis dolore te feugait nulla facilisi.</p>
    </article>

    <article class="feature feature--two">
      <svg class="feature-icon" viewBox="0 0 104 84" width="104" fill="none" stroke="#f7901e" stroke-width="4" stroke-linejoin="round" stroke-linecap="round">
        <path d="M2 22 L16 6 L26 14 L12 30 Z"/>
        <path d="M102 22 L88 6 L78 14 L92 30 Z"/>
        <path d="M26 14 C38 16 46 14 56 16 L42 30 C40 34 46 36 50 32 L60 24 L84 44"/>
        <path d="M78 14 C70 14 64 12 56 16"/>
        <path d="M12 30 L22 44"/>
        <path d="M92 30 L84 44 C82 52 76 50 74 48"/>
        <circle cx="26" cy="52" r="5"/>
        <circle cx="34" cy="60" r="5"/>
        <circle cx="42" cy="67" r="5"/>
        <circle cx="51" cy="73" r="5"/>
        <path d="M74 48 L64 58 M68 54 L58 64 M62 60 L56 70 C60 76 66 70 62 66"/>
      </svg>
      <p class="feature-text">Duis autem vel eum iriure dolor in hendrerit in vulputate velit esse molestie consequat, vel illum dolore eu feugiat nulla facilisis at vero eros et accumsan et iusto odio dignissim qui blan&shy;dit praesent luptatum zzril dele nit augue duis dolore te feugait nulla facilisi.</p>
    </article>

    <article class="feature feature--three">
      <svg class="feature-icon" viewBox="0 0 84 80" width="84" fill="none" stroke="#222d3b" stroke-width="4" stroke-linejoin="round" stroke-linecap="round">
        <rect x="3" y="34" width="10" height="38"/>
        <rect x="13" y="30" width="14" height="46"/>
        <path d="M27 34 L42 22 C48 16 50 8 52 4 C60 4 62 12 58 30 L74 30 C80 30 80 38 74 38 C80 38 80 46 74 46 C80 46 80 54 74 54 C80 54 80 62 74 62 L46 62 C38 62 32 66 27 68"/>
      </svg>
      <p class="feature-text">Duis autem vel eum iriure dolor in hendrerit in vulputate velit esse molestie consequat, vel illum dolore eu feugiat nulla facilisis at vero eros et accumsan et iusto odio dignissim qui blan&shy;dit praesent luptatum zzril del enit augue duis dolore te feugait nulla facilisi.</p>
    </article>

    <div class="footer-rule"></div>
    <div class="page-number">Page 2</div>
  </section>
</body>
</html>
```